Modern web-site for a game changer new health app!

We need a very clean UX / UI design for our company website that will be used to sell our brand to large corporations and their employees. If we find a good match, we'd need you to do the app design and some graphics for ongoing design needs.

For a first of its kind app developed at Brockwell University, making licensed holistic medicine accessible to everyday people through access and curation by democratizing holistic health.

Please read the details attached thoroughly and reach out if you have any questions. Many thanks!
Updates

I've updated our requirements to make it easier, please review new details in the PDF shared. Many thanks!

Final brief refinement just uploaded, much has been simplified with very clear guidelines, please update and apply. thanks much!

Target Market(s)

corporate employees and large C level corporate leaders

Industry/Entity Type

wellness

Number of Pages Required

4 page

Font styles to use
Other font styles liked:
• We need website design now and app and socials after, hoping the designer we choose now can work with us on a regular basis going forward

Requirements
Must have
• clean, modern, minimal rich
Nice to have
• some added touches to give a custom feel
Should not have
• pictures, natural looking images or shapes

```html
<!DOCTYPE html>
<html lang="en">
<head>
<meta charset="utf-8">
<title>Solvie — Health for everyone</title>
<link href="https://fonts.googleapis.com/css2?family=Archivo:wght@600;700;800&family=Inter:wght@400;500;600;700;800&display=swap" rel="stylesheet">
<style>
:root{
  --green:#1f4b44;
  --cream:#fffce0;
  --cream-card:#fffbdc;
  --white:#ffffff;
  --ink:#111111;
  --orange:#f5a21b;
  --sand:#f1d9a3;
  --sand-dark:#d9b47a;
  --grey-num:#c9c9c9;
  --border:#ece7c6;
}
*{box-sizing:border-box;margin:0;padding:0}
html,body{width:1200px;height:4580px;overflow:hidden}
body{font-family:"Inter",sans-serif;color:var(--ink);background:var(--white);position:relative}
section,header,footer{position:relative;width:1200px}
.abs{position:absolute}
h1,h2,h3{font-family:"Archivo",sans-serif;font-weight:700;letter-spacing:-0.5px}
.btn{display:inline-block;background:var(--green);color:#fff;font-size:13px;padding:9px 20px;border-radius:2px;text-decoration:none}
.wordmark{font-family:"Inter",sans-serif;font-weight:800;color:var(--orange);font-size:40px;letter-spacing:1px}

/* nav */
.site-nav{height:136px;background:var(--cream)}
.site-nav .wordmark{left:62px;top:44px}
.nav-links{right:62px;top:60px;display:flex;gap:34px;align-items:center;font-size:16px}
.nav-links a{color:var(--ink);text-decoration:none}
.nav-links a.active{color:var(--green)}
.nav-links a.nav-contact{background:var(--green);color:#fff;padding:7px 16px;border-radius:2px}

/* hero */
.hero{height:448px;background:#0d1410}
.hero-photo{inset:0;background:radial-gradient(circle at 78% 45%,#f4e6ea 0,#e6b7c6 14%,#6b3b48 26%,#1b2a1d 42%,#0d1410 70%),linear-gradient(90deg,#2b4a2a,#0d1410);}
.hero h1{left:60px;top:58px;color:#fff;font-size:92px;line-height:1.23;font-weight:800}
.hero p{left:62px;top:322px;width:420px;color:#fff;font-size:14px;line-height:1.3}
.play{left:850px;top:330px;width:56px;height:56px;border-radius:50%;background:#fff;display:flex;align-items:center;justify-content:center}

/* features */
.features{height:413px;background:var(--cream)}
.feature{width:348px;height:134px;background:var(--white);border:1px solid var(--border);border-radius:4px;display:flex;align-items:center;padding-left:30px;gap:30px;font-size:16px;font-weight:600;line-height:1.4}
.feature svg{flex:none}

/* how it works */
.how{height:446px;background:var(--white)}
.how h2{left:60px;top:68px;font-size:56px}
.how .copy{left:62px;top:150px;width:420px;font-size:13px;line-height:1.75;color:#222}
.how .copy p+p{margin-top:14px}
.how .btn{left:62px;top:312px}
.step-num{font-family:"Archivo",sans-serif;font-weight:700;font-size:72px;color:var(--grey-num);left:694px}
.step{left:804px;width:334px;height:88px;background:var(--cream-card);border:1px solid var(--border);border-radius:4px;display:flex;align-items:center;gap:24px;padding-left:28px;font-size:16px;font-weight:600;line-height:1.35}

.pattern-band{height:90px;background:linear-gradient(180deg,var(--sand) 0%,#f6e2b4 50%,var(--sand-dark) 100%)}

/* trust */
.trust{height:580px;background:var(--cream)}
.trust h2{left:60px;top:86px;font-size:59px;line-height:1.2;font-weight:800}
.trust-card{top:286px;width:348px;height:217px;background:var(--white);border:1px solid var(--border);border-radius:4px;display:flex;flex-direction:column;align-items:center;justify-content:center;gap:26px;font-size:19px;font-weight:600}
.trusted{left:0;width:1200px;top:530px;text-align:center;font-size:21px;font-weight:600}

/* enterprise */
.enterprise{height:554px;background:var(--white)}
.enterprise h2{left:62px;top:64px;font-size:56px;line-height:1.22}
.enterprise .lead{left:62px;top:222px;width:320px;font-size:19px;line-height:1.5}
.enterprise .body{left:62px;top:298px;width:420px;font-size:13px;line-height:1.75;color:#222}
.enterprise .body p+p{margin-top:14px}
.enterprise .btn{left:62px;top:434px}
.spa-art{left:560px;top:94px;width:562px;height:372px;border-radius:50%;background:radial-gradient(ellipse at center,#e9c48f 0,#f1d7c8 30%,#f7efe9 55%,#fff 72%)}

/* human care */
.care{height:383px;background:var(--cream)}
.care h2{left:60px;top:56px;font-size:56px;line-height:1.24}
.care .copy{left:62px;top:206px;font-size:13px;line-height:2.2}
.care .btn{left:62px;top:282px}
.rings{left:838px;top:38px;width:284px;height:284px;background:radial-gradient(circle,#d8d3b5 0,#f3efd4 60%,#fbf8e2 100%)}

/* stats */
.stats{height:721px;background:var(--white)}
.stat-panel{background:var(--green);color:#fff;border-radius:2px}
.stat-main{left:62px;top:81px;width:665px;height:282px}
.stat-main .claim{left:30px;top:76px;width:250px;font-family:"Archivo",sans-serif;font-weight:600;font-size:26px;line-height:1.25}
.big{font-family:"Archivo",sans-serif;font-weight:700;font-size:74px}
.stat-main .p80{left:306px;top:60px}
.stat-main .p20{left:494px;top:60px}
.stat-main .mark{left:310px;top:188px;font-size:28px}
.stat-main .note{left:496px;top:184px;font-size:16px;line-height:1.45}
.stat-side{left:752px;top:81px;width:384px;height:282px}
.stat-side .head{left:30px;top:34px;width:330px;text-align:center;font-family:"Archivo",sans-serif;font-weight:600;font-size:26px;line-height:1.25}
.stat-side .five{left:28px;top:136px;font-size:104px}
.stat-side .star{left:98px;top:192px}
.stat-side .note{left:186px;top:178px;font-size:16px;line-height:1.45}
.quote{left:62px;top:389px;width:1074px;height:332px}
.quote .mk{font-family:"Archivo",sans-serif;font-weight:800;font-size:200px;color:#5f8178;line-height:1}
.quote .open{left:40px;top:10px}
.quote .close{right:40px;top:10px}
.quote .text{left:240px;top:48px;width:600px;text-align:center;font-size:13px;line-height:1.85}
.quote .who{left:0;width:1074px;top:254px;text-align:center;font-size:16px;line-height:1.55}
.quote .who b{font-weight:700}
.arrow-btn{top:262px;width:44px;height:44px;border-radius:50%;background:#fff;display:flex;align-items:center;justify-content:center}

/* contact */
.contact-section{height:503px;background:var(--cream);margin-top:87px}
.contact-section h2{left:62px;top:78px;font-size:56px;line-height:1.55}
.contact-section .copy{left:62px;top:262px;width:400px;font-size:13px;line-height:1.8}
.contact-section .email{left:62px;top:396px;display:flex;align-items:center;gap:14px;font-size:14px}
.field{left:611px;width:525px;height:40px;background:var(--white);display:flex;align-items:center;gap:16px;padding-left:16px;font-size:12px;color:#888}
.field.tall{height:98px;align-items:flex-start;padding-top:16px}
.submit{left:611px;top:410px;width:525px;height:34px;background:var(--green);color:#fff;font-size:13px;display:flex;align-items:center;justify-content:center}

/* footer */
.site-footer{height:130px;background:var(--green)}
.site-footer .wordmark{left:60px;top:42px}
.site-footer .legal{left:397px;top:55px;color:#fff;font-size:16px}
.newsletter{left:830px;top:46px;display:flex;height:34px}
.newsletter span{width:190px;background:#fff;font-size:11px;color:#999;display:flex;align-items:center;padding-left:10px;border-right:1px solid #ccc}
.newsletter b{width:116px;background:#fff;color:var(--green);font-size:12px;display:flex;align-items:center;justify-content:center;font-weight:600}
</style>
</head>
<body>

<header class="site-nav">
  <div class="abs wordmark">SOLVIE</div>
  <nav class="abs nav-links">
    <a class="active" href="#">Home</a><a href="#">Membership</a><a href="#">Organizations</a><a class="nav-contact" href="#">Contact</a>
  </nav>
</header>

<section class="hero">
  <div class="abs hero-photo" role="img" aria-label="Close-up photograph of a pink and white blossom among dark leaves"></div>
  <h1 class="abs">Health for<br>everyone</h1>
  <p class="abs">All-Inclusive Holistic Wellness&nbsp; $25 / month Time tested science changing the lives of millions at a price everyone can afford.</p>
  <div class="abs play"><svg width="18" height="18" viewBox="0 0 18 18"><path d="M5 2l11 7-11 7z" fill="#111"/></svg></div>
</section>

<section class="features">
  <div class="abs feature" style="left:62px;top:66px">
    <svg width="40" height="40" viewBox="0 0 40 40" fill="none" stroke="#1f4b44" stroke-width="2.5"><path d="M6 8h28v18H16l-8 7v-7H6z"/><path d="M12 15h16M12 20h10"/></svg>1 on 1 with Holistic Doctors<br>&amp; Unlimited Texting</div>
  <div class="abs feature" style="left:426px;top:66px">
    <svg width="40" height="40" viewBox="0 0 40 40" fill="none" stroke="#1f4b44" stroke-width="2.5"><rect x="12" y="4" width="16" height="6"/><rect x="8" y="10" width="24" height="26" rx="3"/><circle cx="20" cy="23" r="5"/></svg>Personalized Custom<br>Supplements</div>
  <div class="abs feature" style="left:790px;top:66px">
    <svg width="40" height="40" viewBox="0 0 40 40" fill="none" stroke="#1f4b44" stroke-width="2.5"><path d="M10 4v26a4 4 0 008 0V4M8 4h12M10 16h8"/><path d="M26 20h8v14h-8z"/></svg>Gut, Hormone &amp;<br>Cellular Lab Tests</div>
  <div class="abs feature" style="left:62px;top:216px">
    <svg width="40" height="40" viewBox="0 0 40 40" fill="none" stroke="#1f4b44" stroke-width="2.5"><circle cx="12" cy="10" r="4"/><path d="M6 36V20h12v16M18 22l8-6M22 6h14v16H22"/></svg>Unlimited Classes</div>
  <div class="abs feature" style="left:426px;top:216px">
    <svg width="40" height="40" viewBox="0 0 40 40" fill="none" stroke="#1f4b44" stroke-width="2.5"><circle cx="20" cy="12" r="4"/><path d="M8 34h24M12 28c2-8 14-8 16 0M8 22l6 2M32 22l-6 2M20 2v3M8 8l2 2M32 8l-2 2"/></svg>Free Yoga, Meditation &amp;<br>Health Essentials By Star<br>Practitioners</div>
  <div class="abs feature" style="left:790px;top:216px">
    <svg width="40" height="40" viewBox="0 0 40 40" fill="none" stroke="#1f4b44" stroke-width="2.5"><rect x="4" y="6" width="22" height="14"/><circle cx="10" cy="26" r="3"/><circle cx="20" cy="26" r="3"/><circle cx="32" cy="12" r="3"/><path d="M5 36v-4h10v4M15 36v-4h10v4M28 36V20h8v16"/></svg>Workshops</div>
</section>

<section class="how">
  <h2 class="abs">How It Works</h2>
  <div class="abs copy">
    <p>Sign-up and get a full read of your unique constitution and what makes it thrive with a custom plan made one on one with your on-demand holistic Doctor/Educator.</p>
    <p>Unlimited texting to address your plan or any other concern you have about your health.</p>
  </div>
  <a class="abs btn" href="#">View Plan</a>
  <div class="abs step-num" style="top:78px">01</div>
  <div class="abs step-num" style="top:184px">02</div>
  <div class="abs step-num" style="top:290px">03</div>
  <div class="abs step" style="top:75px"><svg width="30" height="30" viewBox="0 0 30 30" fill="none" stroke="#1f4b44" stroke-width="2.5"><path d="M3 15h15M13 10l5 5-5 5M18 4h9v22h-9"/></svg>Sign Up</div>
  <div class="abs step" style="top:180px"><svg width="30" height="30" viewBox="0 0 30 30" fill="none" stroke="#1f4b44" stroke-width="2.5"><rect x="6" y="4" width="18" height="22"/><path d="M10 11h10M10 16h10M10 21h6"/></svg>Get a full read of<br>your constitution</div>
  <div class="abs step" style="top:287px"><svg width="30" height="30" viewBox="0 0 30 30" fill="none" stroke="#1f4b44" stroke-width="2.5"><path d="M4 18L16 6h10v10L14 28z"/><circle cx="21" cy="11" r="2"/></svg>Get a customer plan</div>
</section>

<div class="pattern-band" role="img" aria-label="Decorative band of repeating sand-coloured arches"></div>

<section class="trust">
  <h2 class="abs">Our Clients Trust Us to Provide Holistic<br>Health for Their Team, So Should You!</h2>
  <div class="abs trust-card" style="left:62px">
    <svg width="62" height="62" viewBox="0 0 62 62" fill="#1f4b44"><path d="M6 6h18v8a5 5 0 010 10v8H6zM30 32h8a5 5 0 0110 0h8v24H30z"/><path d="M6 36h20v20H6z"/></svg>Any Challenge</div>
  <div class="abs trust-card" style="left:426px">
    <svg width="62" height="62" viewBox="0 0 62 62"><circle cx="31" cy="31" r="29" fill="#1f4b44"/><path d="M31 14v17l10 8" stroke="#fff" stroke-width="3" fill="none"/></svg>Anytime</div>
  <div class="abs trust-card" style="left:790px">
    <svg width="62" height="62" viewBox="0 0 62 62"><path d="M31 4a16 16 0 0116 16c0 12-16 28-16 28S15 32 15 20A16 16 0 0131 4z" fill="#1f4b44"/><circle cx="31" cy="20" r="6" fill="#fff"/><path d="M4 58h54" stroke="#1f4b44" stroke-width="4"/></svg>Anywhere</div>
  <div class="abs trusted">Trusted by :-&nbsp; Northfield Outfitters</div>
</section>

<section class="enterprise">
  <h2 class="abs">Solvie for<br>Enterprise</h2>
  <p class="abs lead">We're all feeling a strain on our health these days</p>
  <div class="abs body">
    <p>Leaders of industry aren't accidental, they know employee retention &amp; experience work in their favor.</p>
    <p>In these tumultuous times, Verdawell brings much-needed relief and benefits to teams that bring their all in return.</p>
  </div>
  <a class="abs btn" href="#">Solvie for Enterprise</a>
  <div class="abs spa-art" role="img" aria-label="Spa arrangement of flowers, candles, bath salts and rolled towels"></div>
</section>

<section class="care">
  <h2 class="abs">Human Care<br>Powered by Technology</h2>
  <div class="abs copy">All Your Mind Body Needs Met In One Place<br>All practitioners work collaboratively to provide the best care.</div>
  <a class="abs btn" href="#">View More</a>
  <div class="abs rings" role="img" aria-label="Decorative illustration of concentric rings"></div>
</section>

<div class="pattern-band" role="img" aria-label="Decorative band of repeating sand-coloured arches"></div>

<section class="stats">
  <div class="abs stat-panel stat-main">
    <div class="abs claim">Clinically proven to help people not only feel better, but thrive.</div>
    <div class="abs big p80">80%</div>
    <div class="abs big p20">20%</div>
    <div class="abs wordmark mark">SOLVIE</div>
    <div class="abs note">Leading corporate<br>health programs</div>
  </div>
  <div class="abs stat-panel stat-side">
    <div class="abs head">Members love the easy &amp; effective experience.</div>
    <div class="abs big five">5</div>
    <svg class="abs star" width="44" height="44" viewBox="0 0 24 24"><path d="M12 2l3 7h7l-5.5 4.5 2 7.5L12 17l-6.5 4 2-7.5L2 9h7z" fill="#f6c000"/></svg>
    <div class="abs note">average rating after<br>every care session.</div>
  </div>
  <div class="abs stat-panel quote">
    <div class="abs mk open">“</div>
    <div class="abs mk close">”</div>
    <p class="abs text">Anytime I'm feeling tired or stressed I just get up and pass by the classes by Verdawell and I'm instantly perked up and happy again! Verdawell has been an excellent enhancement at Northfield Outfitters and well needed for everyone. Employees rave about it and frequently ask for more to be added and are getting along better. Ultimately they are more excited about coming to work, automatically enhancing their performance.</p>
    <div class="abs who"><b>MAREN</b><br>Human Resources | Northfield Outfitters</div>
    <div class="abs arrow-btn" style="left:62px"><svg width="16" height="16" viewBox="0 0 16 16"><path d="M10 2L4 8l6 6" stroke="#111" stroke-width="1.6" fill="none"/></svg></div>
    <div class="abs arrow-btn" style="right:52px"><svg width="16" height="16" viewBox="0 0 16 16"><path d="M6 2l6 6-6 6" stroke="#111" stroke-width="1.6" fill="none"/></svg></div>
  </div>
</section>

<section class="contact-section">
  <h2 class="abs">We'd Love To<br>Hear From You</h2>
  <p class="abs copy">Tell us a little about you and your company to see if you qualify for our membership-based model at no cost to your company.</p>
  <div class="abs email">
    <svg width="34" height="34" viewBox="0 0 34 34"><circle cx="17" cy="17" r="15" fill="none" stroke="#1f4b44" stroke-width="2"/><rect x="10" y="12" width="14" height="10" fill="none" stroke="#1f4b44" stroke-width="1.8"/><path d="M10 12l7 6 7-6" fill="none" stroke="#1f4b44" stroke-width="1.8"/></svg>info@solvieforhealth.net</div>
  <div class="abs field" style="top:66px"><svg width="12" height="12" viewBox="0 0 12 12" fill="#1f4b44"><circle cx="6" cy="3.5" r="3"/><path d="M0 12a6 5 0 0112 0z"/></svg>Name</div>
  <div class="abs field" style="top:122px"><svg width="12" height="12" viewBox="0 0 12 12" fill="#1f4b44"><rect y="2" width="12" height="9"/></svg>e-Mail</div>
  <div class="abs field" style="top:178px"><svg width="12" height="12" viewBox="0 0 12 12" fill="#1f4b44"><path d="M6 0a4 4 0 014 4c0 3-4 8-4 8S2 7 2 4a4 4 0 014-4z"/></svg>How many people in your location?</div>
  <div class="abs field" style="top:234px"><svg width="12" height="12" viewBox="0 0 12 12" fill="#1f4b44"><circle cx="6" cy="3.5" r="3"/><path d="M0 12a6 5 0 0112 0z"/></svg>How many locations?</div>
  <div class="abs field tall" style="top:290px"><svg width="12" height="12" viewBox="0 0 12 12" fill="#1f4b44"><path d="M0 1h12v8H4l-3 3V9H0z"/></svg>Anything else we can help with you?</div>
  <div class="abs submit">Submit</div>
</section>

<footer class="site-footer">
  <div class="abs wordmark">SOLVIE</div>
  <div class="abs legal">© 2025 Solvie | All rights reserved.</div>
  <div class="abs newsletter"><span>Enter your e-mail here</span><b>Subscribe</b></div>
</footer>

</body>
</html>
```